Visitenkarten-Design für das Business mit Gesundheit& Beauty
Zielgruppe
Ich bin selbständige Vertriebspartnerin von Vk. Die Visitenkarten sollen nicht zu verspielt wirken, eher geschäftlich. Dennoch könnte eine Verbindung zu den Bereichen Gesundheit & Beuuty dazukommen .
Hauptproduktmerkmal ist zum Beispiel die Aloe Vera, Naturprodukte.. mehr Infos auf : www.bettina-kolmar-beispiel.de
Instagram :bettikolmar
Eventuell könnte mein Slogan mit 'just more' noch einfließen, muss aber nicht. Bin für Ideen offen...
Aufgabenstellung
elegant und zeitlos, aber weich
Vielleicht eine goldene Aloe Vera irgendwie mit drauf?
Habe bei den dateien mal ein paar Screenshots hinzugefügt was ich recht schön fand

```html
<!DOCTYPE html>
<html lang="de">
<head>
<meta charset="utf-8">
<title>Bettina Kolmar – Visitenkarten</title>
<link href="https://fonts.googleapis.com/css2?family=Jost:wght@300;400;600&family=Raleway:wght@300&display=swap" rel="stylesheet">
<style>
  :root {
    --backdrop: #dedede;
    --pink-light: #fdeef3;
    --pink-mid: #f7cdda;
    --pink-deep: #f0b0c4;
    --gold: #b8996b;
    --gold-light: #d9c29a;
    --ink: #1e1c1d;
    --contact: #9a7f84;
  }
  * { box-sizing: border-box; margin: 0; padding: 0; }
  html, body { width: 1200px; height: 842px; overflow: hidden; }
  body {
    background: var(--backdrop);
    font-family: "Jost", sans-serif;
    color: var(--ink);
    position: relative;
  }
  .card {
    position: absolute;
    width: 500px;
    height: 300px;
    border-radius: 3px;
    background: linear-gradient(200deg, var(--pink-deep) 0%, var(--pink-mid) 45%, var(--pink-light) 100%);
    box-shadow: 0 2px 0 #fff, 0 4px 0 #f2f2f2, 0 10px 24px rgba(0,0,0,0.12);
    overflow: hidden;
  }
  .card--front { left: 60px; top: 90px; }
  .card--back { left: 640px; top: 90px; }

  .wordmark {
    position: absolute;
    display: flex;
    align-items: center;
    gap: 14px;
  }
  .wordmark__circle {
    width: 22px; height: 22px;
    border: 2px solid var(--gold);
    border-radius: 50%;
    flex: none;
  }
  .wordmark__name {
    font-weight: 400;
    letter-spacing: 0.12em;
    text-transform: uppercase;
    color: var(--ink);
    white-space: nowrap;
  }
  .card--front .wordmark { left: 0; right: 0; top: 128px; justify-content: center; }
  .card--front .wordmark__name { font-size: 30px; }

  .card--back .wordmark { right: 28px; top: 36px; }
  .card--back .wordmark__name { font-size: 32px; }

  .aloe-photo {
    position: absolute;
    left: 30px; bottom: 0;
    width: 250px; height: 190px;
    background: radial-gradient(ellipse at 50% 55%, var(--gold-light) 0%, rgba(200,170,125,0.7) 40%, rgba(240,200,205,0) 72%);
  }
  .tagline {
    position: absolute;
    right: 28px; top: 100px;
    font-size: 11px;
    font-weight: 600;
    letter-spacing: 0.32em;
    text-transform: uppercase;
    color: var(--ink);
  }
  .contact {
    position: absolute;
    right: 28px; top: 136px;
    font-family: "Raleway", sans-serif;
    font-weight: 300;
    font-size: 12px;
    line-height: 1.9;
    color: var(--contact);
    border-collapse: collapse;
  }
  .contact th { text-align: left; font-weight: 300; padding-right: 14px; }
  .contact td { text-align: left; }

  .logo-lockup {
    position: absolute;
    right: 110px; top: 600px;
    display: flex;
    align-items: center;
    gap: 18px;
  }
  .logo-lockup .wordmark__circle { width: 34px; height: 34px; }
  .logo-lockup .wordmark__name { font-size: 40px; letter-spacing: 0.06em; }
</style>
</head>
<body>
  <section class="card card--front" aria-label="Visitenkarte Vorderseite">
    <div class="wordmark">
      <span class="wordmark__circle"></span>
      <span class="wordmark__name">Bettina Kolmar</span>
    </div>
  </section>

  <section class="card card--back" aria-label="Visitenkarte Rückseite">
    <div class="aloe-photo" role="img" aria-label="Goldfarbene Aloe-Vera-Pflanze, die sich im Wasser spiegelt"></div>
    <div class="wordmark">
      <span class="wordmark__circle"></span>
      <span class="wordmark__name">Bettina Kolmar</span>
    </div>
    <p class="tagline">Health, Beauty &amp; More</p>
    <table class="contact">
      <tr><th>Tel.:</th><td>+49 170 5550142</td></tr>
      <tr><th>E-mail:</th><td>info@bettina-kolmar-beispiel.de</td></tr>
      <tr><th>Web:</th><td>www.bettina-kolmar-beispiel.de</td></tr>
    </table>
  </section>

  <div class="logo-lockup wordmark" aria-label="Bettina Kolmar">
    <span class="wordmark__circle"></span>
    <span class="wordmark__name">Bettina Kolmar</span>
  </div>
</body>
</html>
```